New Webpage for High Class Expert Witness Services Company

We are looking for a minimalist design for a webpage that just has our logo and an entry form offer to connect with one of our Liaisons.
The entry form should just ask for Name, Email, Contact Info and Description of Project.

Company Name is: The Marlowe Crest Advisory Services

Number of Pages Required

1 page

```html
<!DOCTYPE html>
<html lang="en">
<head>
<meta charset="utf-8">
<title>Marlowe Crest Advisory Services — Connect With a Liaison</title>
<link rel="stylesheet" href="https://fonts.googleapis.com/css2?family=Cinzel:wght@400;600;700&family=Roboto:wght@400&display=swap">
<style>
  :root {
    --bg: #000000;
    --bg-glow: #2a2a2a;
    --silver-light: #e4e4e6;
    --silver-mid: #b9b9bc;
    --silver-dark: #8c8c90;
    --eyebrow: #a9a9ad;
    --field-border: #a4a4a8;
    --field-text: #ffffff;
    --button-dark: #121212;
    --rule: #3a3a3a;
    --footer-text: #a6a6a6;
  }
  * { box-sizing: border-box; margin: 0; padding: 0; }
  html, body {
    width: 1200px;
    height: 740px;
    overflow: hidden;
    background: var(--bg);
  }
  .page {
    position: relative;
    width: 1200px;
    height: 740px;
    overflow: hidden;
    background:
      radial-gradient(ellipse 360px 300px at 330px 250px, rgba(70,70,70,0.55), rgba(0,0,0,0) 70%),
      var(--bg);
    font-family: "Roboto", Arial, sans-serif;
  }
  .backdrop-emblem {
    position: absolute;
    left: 600px;
    top: 0;
    width: 600px;
    height: 678px;
    background:
      radial-gradient(ellipse 260px 340px at 330px 330px, rgba(60,60,60,0.55), rgba(20,20,20,0) 75%),
      linear-gradient(100deg, rgba(30,30,30,0.9) 0%, rgba(12,12,12,0.6) 45%, rgba(40,40,40,0.5) 100%);
  }
  .brand {
    position: absolute;
    left: 141px;
    top: 68px;
    display: flex;
    align-items: center;
    gap: 14px;
  }
  .brand-mark {
    width: 44px;
    height: 44px;
    background: var(--silver-mid);
  }
  .brand-name {
    font-family: "Cinzel", Georgia, serif;
    font-weight: 600;
    font-size: 24px;
    line-height: 1;
    letter-spacing: 1px;
    color: var(--silver-light);
    text-transform: uppercase;
  }
  .hero {
    position: absolute;
    left: 139px;
    top: 236px;
  }
  .hero-eyebrow {
    font-family: "Cinzel", Georgia, serif;
    font-size: 16px;
    letter-spacing: 1.5px;
    color: var(--eyebrow);
    text-transform: uppercase;
  }
  .hero-title {
    margin-top: 10px;
    font-family: "Cinzel", Georgia, serif;
    font-weight: 400;
    font-size: 58px;
    line-height: 57px;
    text-transform: uppercase;
    background: linear-gradient(90deg, var(--silver-dark) 0%, var(--silver-light) 55%, var(--silver-mid) 100%);
    -webkit-background-clip: text;
    background-clip: text;
    color: transparent;
  }
  .liaison {
    position: absolute;
    left: 733px;
    top: 158px;
    width: 336px;
  }
  .liaison-title {
    font-family: "Cinzel", Georgia, serif;
    font-weight: 400;
    font-size: 25px;
    color: var(--silver-light);
    text-transform: uppercase;
    white-space: nowrap;
  }
  .liaison-form {
    margin-top: 17px;
    margin-left: 5px;
    display: flex;
    flex-direction: column;
    gap: 13px;
  }
  .field {
    width: 329px;
    height: 42px;
    background: transparent;
    border: 1px solid var(--field-border);
    border-radius: 2px;
    padding: 0 17px;
    font-family: "Roboto", Arial, sans-serif;
    font-size: 13px;
    color: var(--field-text);
    outline: none;
  }
  .field::placeholder { color: var(--field-text); opacity: 1; }
  .field-description {
    height: 88px;
    padding-top: 12px;
    resize: none;
  }
  .submit-button {
    width: 332px;
    height: 44px;
    margin-top: 0;
    border: none;
    border-radius: 2px;
    background: linear-gradient(110deg, var(--silver-light) 0%, #d2d2d4 40%, #bdbdc0 55%, var(--silver-dark) 100%);
    font-family: "Cinzel", Georgia, serif;
    font-weight: 700;
    font-size: 15px;
    letter-spacing: 0.5px;
    color: var(--button-dark);
    cursor: pointer;
  }
  .site-footer {
    position: absolute;
    left: 0;
    top: 678px;
    width: 1200px;
    height: 62px;
    border-top: 1px solid var(--rule);
    display: flex;
    align-items: center;
    justify-content: center;
    font-size: 12px;
    color: var(--footer-text);
  }
</style>
</head>
<body>
  <div class="page">
    <div class="backdrop-emblem" role="img" aria-label="Faint large brand emblem decoration in dark grey tones"></div>

    <header class="brand">
      <span class="brand-mark" aria-hidden="true"></span>
      <span class="brand-name">Marlowe Crest</span>
    </header>

    <section class="hero">
      <p class="hero-eyebrow">Marlowe Crest Advisory Services</p>
      <h1 class="hero-title">Seamless<br>Medical Expert<br>Integration</h1>
    </section>

    <section class="liaison">
      <h2 class="liaison-title">Connect With a Liaison</h2>
      <form class="liaison-form">
        <input class="field" type="text" placeholder="Name*">
        <input class="field" type="email" placeholder="Email*">
        <input class="field" type="tel" placeholder="Phone number*">
        <textarea class="field field-description" placeholder="Description of Project"></textarea>
        <button class="submit-button" type="button">Submit</button>
      </form>
    </section>

    <footer class="site-footer">© 2026 Marlowe Crest Advisory Services. All Rights Reserved</footer>
  </div>
</body>
</html>
```